3 Page Design for Ninth Bay Capital

We want a Home Page, About Page, and Products & Services Page for Ninth Bay Capital. Please refer to the attached docs for more info.
If done in Figma, would like Figma files that can easily be ported to Wordpress.

```html
<!DOCTYPE html>
<html lang="en">
<head>
<meta charset="utf-8">
<title>Ninth Bay Capital — Home</title>
<link href="https://fonts.googleapis.com/css2?family=Inter:wght@300;400;500;600&display=swap" rel="stylesheet">
<style>
:root{
  --bg:#e8dcc8;
  --ink:#2e2b29;
  --body:#4a4542;
  --purple:#6a5b96;
  --red:#9b1b30;
  --tan:#a08a6a;
  --card:#a09d9a;
  --band1:#6f6b68;
  --band2:#a3a09c;
  --band3:#cfc6b8;
  --band4:#e3d9c9;
}
*{box-sizing:border-box;margin:0;padding:0}
html,body{width:1200px;height:2769px;overflow:hidden}
body{background:var(--bg);font-family:"Inter",sans-serif;color:var(--ink);position:relative}
.abs{position:absolute}
.brand{display:flex;align-items:center;gap:12px;font-weight:600;font-size:20px;color:var(--ink)}
.brand-mark{width:40px;height:40px;border-radius:50%;background:var(--ink)}
.nav{display:flex;gap:34px;font-size:14px;font-weight:500}
.nav a{color:var(--ink);text-decoration:none}
.nav .active{color:var(--red);border-top:2px solid var(--red);padding-top:6px;margin-top:-8px}
.btn{display:inline-flex;align-items:center;justify-content:center;color:#fff;font-size:14px;font-weight:500;border-radius:3px;height:43px;padding:0 23px;text-decoration:none}
.btn-red{background:var(--red)}
.btn-purple{background:var(--purple)}
h1{font-weight:500;font-size:58px;line-height:60px;letter-spacing:-0.5px}
h2{font-weight:500;font-size:46px;letter-spacing:-0.3px;line-height:1.1}
.lead{font-size:17px;line-height:24px;font-weight:300;color:var(--body)}
.tag{border:2px solid var(--tan);color:var(--tan);font-size:19px;border-radius:3px;height:41px;display:flex;align-items:center;justify-content:center;background:var(--bg)}
.photo{border-radius:2px}
.card{position:absolute;top:1891px;width:206px;height:214px;background:var(--card);color:#fff;text-align:center;font-size:18px;line-height:22px;font-weight:300;padding:118px 14px 0}
.card svg{position:absolute;left:77px;top:32px}
.card-active{background:var(--purple)}
.band{position:absolute;height:12px}
</style>
</head>
<body>

<header>
  <div class="brand abs" style="left:149px;top:45px"><span class="brand-mark"></span>Ninth Bay Capital</div>
  <nav class="nav abs" style="left:456px;top:55px">
    <a class="active">HOME</a><a>ABOUT</a><a>PRODUCTS &amp; SERVICES</a><a>CONTACT</a>
  </nav>
  <a class="btn btn-red abs" style="left:894px;top:38px;width:154px;padding:0">GET STARTED&nbsp;&nbsp;<svg width="10" height="16" viewBox="0 0 10 16"><path d="M2 2l6 6-6 6" stroke="#fff" stroke-width="2" fill="none"/></svg></a>
</header>

<section class="hero">
  <div class="photo abs" role="img" aria-label="Athlete sprinting mid-stride over a faint line pattern" style="left:455px;top:160px;width:595px;height:520px;background:radial-gradient(ellipse at 65% 45%,#2e6f86 0%,#6a5b56 22%,#dccdb5 55%,var(--bg) 75%)"></div>
  <h1 class="abs" style="left:147px;top:170px">Built for Legacy.<br>Designed for<br>Performance.</h1>
  <p class="lead abs" style="left:150px;top:372px;width:410px">Athletes and entrepreneurs build lasting success on and off the field — merging discipline, business structure, and automated systems to create generational wealth.</p>
  <a class="btn btn-purple abs" style="left:150px;top:498px;width:215px;padding:0">START YOUR TRANSITION</a>
  <a class="btn btn-red abs" style="left:150px;top:557px;width:247px;padding:0">LEARN HOW WE BUILD LEGACY</a>
</section>

<section class="mission">
  <div class="abs" style="left:149px;top:772px;width:899px;height:258px;border:1.5px solid var(--tan);border-radius:3px"></div>
  <div class="abs" style="left:157px;top:1030px;width:883px;height:5px;border:1.5px solid var(--tan);border-top:0"></div>
  <div class="abs" style="left:168px;top:1035px;width:872px;height:5px;border:1.5px solid var(--tan);border-top:0"></div>
  <div class="abs" style="left:520px;top:766px;width:160px;height:12px;background:var(--bg)"></div>
  <div class="tag abs" style="left:548px;top:750px;width:104px">Mission</div>
  <h2 class="abs" style="left:149px;top:830px;width:899px;text-align:center">Where Discipline Meets Wealth.</h2>
  <p class="abs" style="left:250px;top:903px;width:700px;text-align:center;font-size:18px;line-height:26px;font-weight:300;color:var(--body)">Ninth Bay Capital bridges performance, business, and wellness to empower high-achievers to move from uncertainty to clarity. Our approach blends the focus of sport, the sophistication of modern business, and the stability of long-term financial strategy.</p>
</section>

<section class="about">
  <div class="abs" style="left:157px;top:1134px;width:451px;height:501px;border:1.5px solid var(--tan)"></div>
  <div class="abs" style="left:184px;top:1145px;width:432px;height:501px;border:1.5px solid var(--tan)"></div>
  <div class="photo abs" role="img" aria-label="Businessman seated at a desk with a laptop in a bright office" style="left:148px;top:1126px;width:451px;height:501px;background:linear-gradient(120deg,#c8c2b5 0%,#e6e2da 35%,#6f7a80 55%,#a9794a 80%,#8c8f86 100%)"></div>
  <div class="tag abs" style="left:670px;top:1127px;width:113px">About Us</div>
  <h2 class="abs" style="left:669px;top:1192px">Performance.<br>Structure.<br>Automation.</h2>
  <div class="abs" style="left:670px;top:1367px;width:47px;height:2px;background:var(--tan)"></div>
  <p class="abs" style="left:669px;top:1402px;width:385px;font-size:18px;line-height:26px;font-weight:300;color:var(--body)">Ninth Bay Capital — exists to guide high-performers through the moments that shape their legacy. We bridge the worlds of performance, wealth, and wellness, helping athletes and entrepreneurs build success that lasts far beyond the game.</p>
  <a class="btn btn-red abs" style="left:671px;top:1595px;width:128px;padding:0">READ MORE</a>
</section>

<section class="offer">
  <div class="tag abs" style="left:523px;top:1729px;width:156px">What We Offer</div>
  <h2 class="abs" style="left:0;top:1800px;width:1200px;text-align:center">Refined Strategy for Athletes in Transition</h2>
  <div class="card" style="left:155px"><svg width="52" height="52" viewBox="0 0 52 52" fill="none" stroke="#fff" stroke-width="1.5"><circle cx="26" cy="26" r="17"/><circle cx="26" cy="26" r="10"/><path d="M20 30l5-5 3 3 5-6"/></svg>Build sustainable business and financial structures</div>
  <div class="card card-active" style="left:384px"><svg width="52" height="52" viewBox="0 0 52 52" fill="none" stroke="#fff" stroke-width="1.5"><circle cx="26" cy="28" r="18"/><circle cx="26" cy="28" r="10"/><circle cx="26" cy="28" r="3"/><path d="M26 28l16-16M38 10v6h6"/></svg>Develop strategic discipline beyond the field</div>
  <div class="card" style="left:614px"><svg width="52" height="52" viewBox="0 0 52 52" fill="none" stroke="#fff" stroke-width="1.5"><circle cx="14" cy="38" r="6"/><path d="M22 44l24-22M30 20l8-10 4 4"/><path d="M40 6l2 3 3 1-3 1-2 3-1-3-3-1 3-1z"/></svg>Leverage automation for long-term success</div>
  <div class="card" style="left:844px"><svg width="52" height="52" viewBox="0 0 52 52" fill="none" stroke="#fff" stroke-width="1.5"><path d="M4 24a22 18 0 0 1 44 0z"/><path d="M26 6v18"/><circle cx="18" cy="32" r="3"/><circle cx="26" cy="30" r="3"/><circle cx="34" cy="32" r="3"/><path d="M14 46v-7h8v7M22 46v-9h8v9M30 46v-7h8v7"/></svg>Design a life that scales with their ambition</div>
</section>

<section class="cta">
  <div class="band" style="left:0;top:2187px;width:291px;background:var(--band1)"></div>
  <div class="band" style="left:299px;top:2187px;width:295px;background:var(--band2)"></div>
  <div class="band" style="left:602px;top:2187px;width:296px;background:var(--band3)"></div>
  <div class="band" style="left:906px;top:2187px;width:294px;background:var(--band4)"></div>
  <h2 class="abs" style="left:0;top:2258px;width:1200px;text-align:center">Your Legacy Starts With Clarity</h2>
  <p class="abs" style="left:0;top:2328px;width:1200px;text-align:center;font-size:22px;font-weight:300;color:var(--body)">Take the first step toward building the life and business you were meant for.</p>
  <a class="btn btn-purple abs" style="left:388px;top:2390px;width:215px;padding:0">BEGIN YOUR TRANSITION</a>
  <a class="btn btn-red abs" style="left:619px;top:2390px;width:215px;padding:0">BOOK A STRATEGY SESSION</a>
  <div class="band" style="left:0;top:2501px;width:291px;background:var(--band4)"></div>
  <div class="band" style="left:299px;top:2501px;width:295px;background:var(--band3)"></div>
  <div class="band" style="left:602px;top:2501px;width:296px;background:var(--band2)"></div>
  <div class="band" style="left:906px;top:2501px;width:294px;background:var(--band1)"></div>
</section>

<footer>
  <div class="brand abs" style="left:149px;top:2580px"><span class="brand-mark"></span>Ninth Bay Capital</div>
  <nav class="nav abs" style="left:641px;top:2592px"><a>HOME</a><a>ABOUT</a><a>PRODUCTS &amp; SERVICES</a><a>CONTACT</a></nav>
  <div class="abs" style="left:149px;top:2670px;width:899px;height:1px;background:#cbbfa9"></div>
  <p class="abs" style="left:0;top:2710px;width:1200px;text-align:center;font-size:14px;font-weight:300">Copyright © 2025 All Rights Reserved</p>
</footer>

</body>
</html>
```